BOLD & MINIMALIST DESIGN NEEDED

We want a very bold but minimalistic business card design that is impactful and utilizes both sides of the business card. Our current logo is included for your use.

We want bold fonts and good use of negative space. We don't want the logo to overpower the design.

Target Market(s)

Professionals who are building new commercial buildings.

Industry/Entity Type

Construction

Contact Information for Business Card

Name, Title, email, office phone, cell phone, website

Font styles to use
Serif
Sans Serif

Requirements
Must have
• Bold design!

```html
<!DOCTYPE html>
<html lang="en">
<head>
<meta charset="utf-8">
<title>Ridgeline Design + Build – Business Card</title>
<link href="https://fonts.googleapis.com/css2?family=Poppins:wght@300;400;500;600;700&display=swap" rel="stylesheet">
<style>
  :root {
    --backdrop: #2b2b2b;
    --card: #262626;
    --card-edge: #2e2e2e;
    --brand-green: #7ab833;
    --text-light: #e4e4e4;
    --text-muted: #bdbdbd;
    --mark-dark: #4c4c4c;
  }
  * { margin: 0; padding: 0; box-sizing: border-box; }
  html, body {
    width: 1200px;
    height: 576px;
    overflow: hidden;
    background: var(--backdrop);
    font-family: "Poppins", sans-serif;
  }
  .card {
    position: absolute;
    top: 138px;
    height: 294px;
    border-radius: 8px;
    background: linear-gradient(160deg, var(--card-edge), var(--card));
  }
  .card--front { left: 102px; width: 484px; }
  .card--back { left: 596px; width: 480px; }

  /* Front */
  .front-name {
    position: absolute;
    left: 0; right: 0;
    top: 102px;
    text-align: center;
    font-size: 54px;
    font-weight: 700;
    letter-spacing: 2px;
    color: var(--mark-dark);
  }
  .front-url {
    position: absolute;
    left: 0; right: 0;
    top: 252px;
    text-align: center;
    font-size: 13px;
    font-weight: 300;
    letter-spacing: 6px;
    color: var(--text-muted);
  }

  /* Back */
  .person {
    position: absolute;
    right: 30px;
    top: 30px;
    text-align: right;
  }
  .person__name {
    font-size: 21px;
    font-weight: 500;
    color: var(--brand-green);
    line-height: 1.2;
  }
  .person__title {
    font-size: 11.5px;
    font-weight: 400;
    color: var(--text-light);
  }
  .company {
    position: absolute;
    left: 32px;
    top: 206px;
    display: flex;
    align-items: center;
    gap: 8px;
  }
  .company__square {
    width: 14px;
    height: 14px;
    background: var(--brand-green);
  }
  .company__name {
    font-size: 17px;
    font-weight: 600;
    color: var(--text-light);
    letter-spacing: 0.5px;
    line-height: 1.15;
  }
  .contact {
    position: absolute;
    right: 30px;
    top: 216px;
    list-style: none;
  }
  .contact__item {
    display: flex;
    justify-content: flex-end;
    align-items: center;
    gap: 6px;
    height: 16.5px;
    font-size: 12px;
    color: var(--text-light);
  }
  .contact__icon { width: 10px; height: 10px; fill: var(--brand-green); }
</style>
</head>
<body>
  <section class="card card--front">
    <div class="front-name">RIDGELINE</div>
    <div class="front-url">www.ridgelinebuild.com</div>
  </section>

  <section class="card card--back">
    <div class="person">
      <div class="person__name">Lucas Moreno</div>
      <div class="person__title">Director</div>
    </div>

    <div class="company">
      <span class="company__square"></span>
      <span class="company__name">RIDGELINE<br>DESIGN + BUILD</span>
    </div>

    <ul class="contact">
      <li class="contact__item">004-004-0004
        <svg class="contact__icon" viewBox="0 0 10 10"><path d="M1 3c0-1 1-2 4-2s4 1 4 2v1H7V3H3v1H1z M2 5h6l1 4H1z"/></svg>
      </li>
      <li class="contact__item">lucas@ridgelinebuild.com
        <svg class="contact__icon" viewBox="0 0 10 10"><path d="M0 2h10v6H0z M0 2l5 3.5L10 2" stroke="#262626" stroke-width="0.8"/></svg>
      </li>
      <li class="contact__item">www.ridgelinebuild.com
        <svg class="contact__icon" viewBox="0 0 10 10"><circle cx="5" cy="5" r="4.5"/><path d="M0.5 5h9 M5 0.5v9 M5 0.5c-2 2-2 7 0 9 M5 0.5c2 2 2 7 0 9" stroke="#262626" stroke-width="0.6" fill="none"/></svg>
      </li>
    </ul>
  </section>
</body>
</html>
```